Coffee and Plastics

I am looking for a completely new site that shows the products we have. Our current site is www.velmorebrothersbeans.com. We are open minded to what designers come up with. Our current site is www.velmorebrothersbeans.com. You can you the information from there to start the site. I need these tabs on the main home page. ( Home, Coffee & Tea, Condiments, and Paper and Plastics, and Contact.) You can take photos and info from my Current site. In products page.
I will be uploading info and photo for paper and plastics.
Look and feel
Each slider illustrates characteristics of the customer's brand and the style your logo design should communicate.

```html
<!DOCTYPE html>
<html lang="en">
<head>
<meta charset="utf-8">
<title>Velmore Brothers Beans</title>
<link href="https://fonts.googleapis.com/css2?family=Lora:wght@400;700&family=Open+Sans:wght@400;600;700&display=swap" rel="stylesheet">
<style>
:root{
  --cream:#f4eee3;
  --cream-dark:#e9e0cf;
  --brown:#7a4a1c;
  --brown-deep:#3a2a1d;
  --brown-footer:#4a3726;
  --green:#5d7a2a;
  --green-light:#86a83a;
  --nav:#5b3d22;
  --text:#5a4a3a;
  --muted:#b9a890;
  --white:#ffffff;
}
*{box-sizing:border-box;margin:0;padding:0}
html,body{width:824px;height:1200px;overflow:hidden}
body{background:var(--cream);font-family:"Open Sans",Arial,sans-serif;color:var(--text);position:relative}
.wrap{width:770px;margin:0 auto;position:relative}
.topbar{height:26px;background:var(--cream-dark);font-size:8px;color:var(--text)}
.topbar .wrap{display:flex;align-items:center;height:26px;gap:24px}
.topbar .social{margin-left:auto;display:flex;gap:4px}
.topbar .social span{width:11px;height:11px;background:var(--green);display:block}
.brand{height:66px;text-align:center}
.brand h1{font-family:"Lora",Georgia,serif;font-weight:400;font-size:30px;color:var(--brown);padding-top:14px}
.nav{background:var(--nav);height:24px;display:flex}
.nav a{color:var(--white);font-size:9px;font-weight:600;text-decoration:none;flex:1;text-align:center;line-height:24px}
.nav a.active{background:var(--green-light);flex:0 0 70px}
.hero{height:270px;margin-top:4px;position:relative;background:linear-gradient(110deg,#2a1a10 0%,#6b4328 35%,#c9a275 60%,#8c5e3b 85%,#3b2415 100%)}
.hero .arrow{position:absolute;top:126px;width:14px;height:18px;color:#fff;font-size:14px;line-height:18px;text-align:center}
.hero .prev{left:6px}.hero .next{right:6px}
.hero-card{position:absolute;right:80px;top:40px;width:150px;height:170px;background:rgba(255,255,255,.9);text-align:center;padding:20px 10px}
.hero-card h2{font-family:"Lora",Georgia,serif;font-weight:400;font-size:16px;color:var(--brown-deep);line-height:1.25}
.hero-card p{font-size:8px;color:var(--brown);margin-top:12px;line-height:1.4}
.btn{display:inline-block;background:var(--green);color:#fff;font-size:8px;padding:6px 12px;margin-top:14px}
.welcome{margin-top:26px}
.welcome h3{font-size:11px;font-weight:700;color:var(--brown);letter-spacing:.3px}
.welcome .row{display:flex;gap:16px;margin-top:12px}
.welcome .photo{width:120px;height:90px;flex:none;background:linear-gradient(135deg,#3a2412,#a97d4e 55%,#5c3a1e)}
.welcome p{font-size:7.5px;line-height:1.6;color:var(--text)}
.welcome p+p{margin-top:8px}
.section-head{display:flex;align-items:center;justify-content:center;gap:10px;margin-top:40px}
.section-head h3{font-size:11px;font-weight:700;color:var(--green);text-transform:uppercase}
.section-head .rule{flex:1;height:1px;background:var(--brown)}
.round{width:14px;height:14px;border-radius:50%;background:var(--brown);color:#fff;font-size:9px;line-height:14px;text-align:center;flex:none}
.round.light{background:var(--muted)}
.products{margin-top:12px;background:#fff;height:120px;display:flex;align-items:center;justify-content:space-around;padding:0 22px}
.product{width:84px;height:74px;background:radial-gradient(circle at 50% 50%,#f4f1ea 0%,#cfc8b8 55%,#8d7c63 100%)}
.product.dark{background:radial-gradient(circle,#a77a3c 0%,#5a3a18 80%)}
.partners{display:flex;justify-content:center;gap:28px;margin-top:24px;align-items:center}
.partner{width:70px;height:46px;background:#fff;border:1px solid var(--cream-dark);display:flex;align-items:center;justify-content:center}
.partner span{display:block;width:42px;height:22px;border-radius:3px}
.footer{position:absolute;left:0;top:990px;width:824px;height:210px;background:var(--brown-footer);color:var(--muted)}
.footer .cols{display:flex;padding-top:24px}
.footer .col{flex:1}
.footer h4{font-size:9px;font-weight:700;color:#fff;margin-bottom:12px;letter-spacing:.3px}
.footer li{list-style:none;font-size:7.5px;line-height:2}
.footer .icons{display:flex;flex-direction:column;gap:6px;align-items:center;width:40px}
.footer .icons span{width:16px;height:16px;background:#8a7a68;display:block}
.footer input{display:block;width:110px;height:17px;border:none;margin-bottom:6px;font-size:7px;padding:0 5px;color:#aaa}
.footer .btn{margin-top:2px}
.copyright{position:absolute;left:0;bottom:0;width:824px;height:26px;background:var(--brown-deep);font-size:7.5px;color:var(--muted);text-align:center;line-height:26px}
</style>
</head>
<body>
<div class="topbar"><div class="wrap">
  <span>Mon - Fri 8 - 5 Central Time</span><span>Call: 1 (800) 555-0142</span>
  <div class="social"><span></span><span></span><span></span></div>
</div></div>

<header class="brand"><h1>Velmore Brothers Beans</h1></header>

<div class="wrap">
  <nav class="nav">
    <a class="active" href="#">Home</a><a href="#">Coffee &amp; Tea</a><a href="#">Condiments</a><a href="#">Paper</a><a href="#">Plastics</a><a href="#">Contact</a>
  </nav>

  <section class="hero" role="img" aria-label="Cup of coffee on a saucer surrounded by roasted coffee beans">
    <span class="arrow prev">&#8249;</span><span class="arrow next">&#8250;</span>
    <div class="hero-card">
      <h2>Velmore Brothers Beans</h2>
      <p>Be guarantee of all our products with your best of satisfaction</p>
      <span class="btn">Contact Now</span>
    </div>
  </section>

  <section class="welcome">
    <h3>WELCOME TO VELMORE BROTHERS BEANS</h3>
    <div class="row">
      <div class="photo" role="img" aria-label="Burlap sack filled with roasted coffee beans"></div>
      <div>
        <p>We are a family owned and operated business started in 1985. From our roastery in the heart of town we have served hotels, diners and offices with fresh coffee and reliable supplies. Our roasting team blends beans from trusted growers, and our delivery crew brings every order to your door on time. We believe good coffee begins with honest work and lasting partnerships built over many years of service.</p>
        <p>Today we offer a complete line of coffee, tea, condiments, paper and plastic goods for food service. Whether you run a single cafe or a chain of hotels, we tailor each order to your needs and your budget. Our staff is ready to help you pick the right products, set up regular deliveries and keep your guests happy every single day.</p>
      </div>
    </div>
  </section>

  <div class="section-head">
    <span class="round">&#8249;</span><span class="rule"></span><h3>Our Products</h3><span class="rule"></span><span class="round light">&#8250;</span>
  </div>
  <div class="products">
    <div class="product" role="img" aria-label="Round clear plastic container"></div>
    <div class="product" role="img" aria-label="Divided white foam plate"></div>
    <div class="product" role="img" aria-label="Round plastic dish"></div>
    <div class="product" role="img" aria-label="Compartment plastic tray"></div>
    <div class="product" role="img" aria-label="Square compartment tray"></div>
    <div class="product" role="img" aria-label="Multi-section food tray"></div>
    <div class="product dark" role="img" aria-label="Gold catering tray"></div>
  </div>

  <div class="section-head">
    <span class="rule"></span><h3>Serving fine establishments everywhere!</h3><span class="rule"></span>
  </div>
  <div class="partners">
    <div class="partner"><span style="background:#3f7a3a"></span></div>
    <div class="partner"><span style="background:#1f3f7a"></span></div>
    <div class="partner"><span style="background:#2f5a3a"></span></div>
    <div class="partner"><span style="background:#3a4a8a"></span></div>
    <div class="partner"><span style="background:#6a5a8a"></span></div>
    <div class="partner"><span style="background:#4a4a4a"></span></div>
    <div class="partner"><span style="background:#2a5aa0"></span></div>
  </div>
</div>

<footer class="footer">
  <div class="wrap cols">
    <div class="col"><h4>IN BRIEF</h4><ul><li>ABOUT US</li><li>SUCCESS STORIES</li><li>BECOMING A SOLUTION PARTNER</li></ul></div>
    <div class="col"><h4>RESOURCES</h4><ul><li>DOCUMENTATION</li><li>KNOWLEDGE BASE</li><li>PREMIUM SUPPORT</li></ul></div>
    <div class="col"><h4>STAYING IN TOUCH</h4><div class="icons"><span></span><span></span><span></span></div></div>
    <div class="col"><h4>CONTACT US</h4><input value="Enter your name"><input value="Enter your email"><span class="btn">Contact Us</span></div>
  </div>
  <div class="copyright">Copyright &copy; velmorebrothersbeans &nbsp;|&nbsp; Terms &amp; Conditions &nbsp;|&nbsp; Privacy Policy &nbsp;|&nbsp; Cookie Policy &nbsp;|&nbsp; Contact Us</div>
</footer>
</body>
</html>
```